Pine leaf & Snapvista ad needed

I am in need of a simple static image ad to be used for Pineleaf & Snapvista. A photo of a nice roof on a nice house. "Instant Satellite Roof Estimates" "Your house, your time & instant estimate" . Our logo file is here: https://www.filecrate-example.net/share/q73kdm41xv9wpz2tbn8hs/JKsT4mWQpZ2xYcVn8bRfL6d?key=wm5tz81qvjx3c7bnd0ke9fa4r&v=0

Multiple variations will be purchased.

```html
<!DOCTYPE html>
<html lang="en">
<head>
<meta charset="utf-8">
<title>Instant Satellite Roof Estimates</title>
<link rel="stylesheet" href="https://fonts.googleapis.com/css2?family=Anton&family=Roboto+Condensed:wght@400&family=Montserrat:wght@500;700&family=Poppins:wght@400;500&display=swap">
<style>
  :root {
    --teal-deep: #0a4f61;
    --teal-mid: #138aa3;
    --cyan-glow: #7fe3f6;
    --frame-teal: #1596b2;
    --title-blue: #0b3f9c;
    --title-blue-light: #1a6fd6;
    --ribbon-text: #0d6878;
    --white: #ffffff;
    --ink: #1c2430;
  }
  * { margin: 0; padding: 0; box-sizing: border-box; }
  html, body { width: 962px; height: 1200px; overflow: hidden; background: var(--white); }
  .ad {
    position: relative;
    width: 962px;
    height: 1200px;
    overflow: hidden;
    background: radial-gradient(ellipse 560px 520px at 820px 360px, var(--cyan-glow) 0%, #3cbfd9 35%, var(--teal-mid) 62%, var(--teal-deep) 100%);
  }
  .brand {
    position: absolute;
    left: 76px;
    top: 196px;
    color: var(--white);
    font-family: "Montserrat", sans-serif;
    font-weight: 500;
    line-height: 1;
  }
  .brand-name { font-size: 42px; letter-spacing: 1px; }
  .brand-sub { font-size: 16px; letter-spacing: 5px; margin-top: 8px; padding-left: 4px; }
  .headline-instant {
    position: absolute;
    left: 362px;
    top: 66px;
    font-family: "Roboto Condensed", sans-serif;
    font-weight: 400;
    font-size: 130px;
    letter-spacing: -4px;
    line-height: 1;
    color: var(--title-blue);
  }
  .headline-satellite {
    position: absolute;
    left: 364px;
    top: 180px;
    font-family: "Anton", sans-serif;
    font-size: 124px;
    line-height: 1;
    letter-spacing: -1px;
    white-space: nowrap;
    background: linear-gradient(180deg, var(--title-blue-light) 0%, var(--title-blue) 70%);
    -webkit-background-clip: text;
    background-clip: text;
    color: transparent;
  }
  .ribbon {
    position: absolute;
    left: 365px;
    top: 320px;
    width: 523px;
    height: 71px;
  }
  .ribbon-text {
    position: absolute;
    left: 386px;
    top: 324px;
    font-family: "Montserrat", sans-serif;
    font-weight: 700;
    font-size: 54px;
    line-height: 64px;
    color: var(--ribbon-text);
    white-space: nowrap;
  }
  .house-art { position: absolute; left: 0; top: 400px; width: 962px; height: 600px; }
  .tagline-band {
    position: absolute;
    left: 0; top: 990px;
    width: 962px; height: 90px;
    background: var(--teal-deep);
    display: flex;
    align-items: center;
    padding-left: 76px;
    font-family: "Montserrat", sans-serif;
    font-weight: 700;
    font-size: 36px;
    color: var(--white);
  }
  .tagline-divider { width: 2px; height: 48px; background: rgba(255,255,255,0.55); margin: 0 18px; }
  .footer {
    position: absolute;
    left: 0; top: 1080px;
    width: 962px; height: 120px;
    background: var(--white);
    display: flex;
    align-items: center;
    padding: 0 75px 0 76px;
    height: 84px;
    font-family: "Poppins", sans-serif;
    font-size: 19px;
    color: var(--ink);
  }
  .contact { display: flex; align-items: center; gap: 4px; margin-right: 10px; white-space: nowrap; }
  .contact-icon { width: 17px; height: 17px; flex: none; }
  .socials { margin-left: auto; display: flex; gap: 6px; font-size: 11px; font-weight: 500; color: var(--teal-deep); white-space: nowrap; }
</style>
</head>
<body>
<main class="ad">
  <div class="brand">
    <div class="brand-name">KEYSTONE</div>
    <div class="brand-sub">ROOFING</div>
  </div>

  <div class="headline-instant">Instant</div>
  <div class="headline-satellite">SATELLITE</div>

  <svg class="ribbon" viewBox="0 0 523 71" aria-hidden="true">
    <polygon points="0,0 523,0 500,35.5 523,71 0,71" fill="var(--white)"/>
  </svg>
  <div class="ribbon-text">Roof Estimates</div>

  <svg class="house-art" viewBox="0 0 962 600">
    <defs>
      <linearGradient id="photo-tone" x1="0" y1="0" x2="0" y2="1">
        <stop offset="0" stop-color="#7aa9dc"/>
        <stop offset="0.5" stop-color="#56616e"/>
        <stop offset="1" stop-color="#4f5f55"/>
      </linearGradient>
    </defs>
    <polygon points="55,590 55,276 340,44 610,262 610,590" fill="var(--frame-teal)" opacity="0.85"/>
    <rect x="125" y="150" width="837" height="440" fill="url(#photo-tone)" role="img" aria-label="Photo of a two-storey house with a shingled roof and covered porch beside a street of homes, with a satellite dish in the corner"/>
  </svg>

  <div class="tagline-band">
    <span>Your house</span>
    <span class="tagline-divider"></span>
    <span>Your time</span>
    <span class="tagline-divider"></span>
    <span>Instant estimate</span>
  </div>

  <footer class="footer">
    <span class="contact">
      <svg class="contact-icon" viewBox="0 0 20 20" aria-hidden="true"><circle cx="10" cy="10" r="10" fill="var(--ink)"/><path d="M6.5 5.5c.6-.4 1.2-.3 1.5.2l.9 1.6c.2.4.1.9-.3 1.2l-.6.4c.5 1.2 1.4 2.1 2.6 2.6l.4-.6c.3-.4.8-.5 1.2-.3l1.6.9c.5.3.6.9.2 1.5-.6.8-1.6 1.1-2.6.7-2.3-.9-4.1-2.7-5-5-.4-1 0-2 .7-2.6z" fill="var(--white)"/></svg>
      033 555 0147
    </span>
    <span class="contact">
      <svg class="contact-icon" viewBox="0 0 20 20" aria-hidden="true"><circle cx="10" cy="10" r="10" fill="var(--ink)"/><rect x="5" y="6.5" width="10" height="7" rx="1" fill="var(--white)"/><path d="M5.5 7l4.5 3.5L14.5 7" stroke="var(--ink)" stroke-width="1.2" fill="none"/></svg>
      keystone@mailbox.com
    </span>
    <span class="contact">
      <svg class="contact-icon" viewBox="0 0 20 20" aria-hidden="true"><circle cx="10" cy="10" r="10" fill="var(--ink)"/><circle cx="10" cy="10" r="5" stroke="var(--white)" stroke-width="1.2" fill="none"/><path d="M5 10h10M10 5c-2 2.8-2 7.2 0 10M10 5c2 2.8 2 7.2 0 10" stroke="var(--white)" stroke-width="1" fill="none"/></svg>
      www.keystoneroof.net
    </span>
    <span class="socials">
      <span>Snapvista</span>
      <span>Pineleaf</span>
      <span>Linkpro</span>
    </span>
  </footer>
</main>
</body>
</html>
```